Business Cards Design for the electrical wholesaler: clean bold dynamic :)

We need a business card design that would follow our latest brand guidelines. As an electrical wholesaler we want to bring a fresh look and feel into the industry. The design should be clean bold and dynamic. It should come alive with the renewed energy of our green colour. Our grey colour should keep things balanced and complement the notion of maturity and responsibility. We employ Lato as a corporate font however are not bound by this font and we’re open to interpretation here.

Target Market(s)

Electrical contractors

Industry/Entity Type

Business

Contact Information for Business Card

Logo
Name & Surname: Halyna Dorosh
Job Title: Director of Marketing
Email: halya.dorosh@quillmail.example
Cell phone: XXX.XXX.XXXX
Address: 20517 - 87 Ave. Edmonton, AB, Canada. T6K 4N8
Business Phone: 780.555.0184
Website: www.brovix.example

Font styles to use
Other font styles liked:
• Lato

Requirements
Must have
• Logo & website
Nice to have
• Brand elements - some of them you may find in the attached Brand Guidelines (e.g. three lines on the background signifying "W")

```html
<!DOCTYPE html>
<html lang="en">
<head>
<meta charset="utf-8">
<title>Brovix Business Card</title>
<link href="https://fonts.googleapis.com/css2?family=Lato:wght@300;400;700&display=swap" rel="stylesheet">
<style>
  :root {
    --backdrop: #2a2a2a;
    --paper: #f4f4f4;
    --green: #8cc43f;
    --green-back: #85bd3b;
    --grey: #4d4d4f;
    --grey-text: #4a4a4a;
    --rule: #8a8a8a;
    --white: #ffffff;
  }
  * { margin: 0; padding: 0; box-sizing: border-box; }
  html, body {
    width: 1200px; height: 960px; overflow: hidden;
    background: var(--backdrop);
    font-family: "Lato", sans-serif;
  }
  .canvas { position: relative; width: 1200px; height: 960px; }
  .card {
    position: absolute; width: 600px; height: 342px;
    border-radius: 22px; overflow: hidden;
  }
  .card-front { left: 314px; top: 113px; background: var(--paper); }
  .card-back { left: 311px; top: 472px; background: var(--green-back); }

  .brand {
    position: absolute; right: 36px; top: 44px;
    display: flex; align-items: center; gap: 12px;
  }
  .brand-mark { width: 34px; height: 34px; background: var(--green); }
  .brand-name { font-size: 50px; font-weight: 400; color: var(--grey); line-height: 1; letter-spacing: -1px; }

  .name-bar { position: absolute; left: 0; top: 153px; width: 14px; height: 37px; background: var(--green); }
  .person { position: absolute; left: 36px; top: 151px; }
  .person-name { font-size: 20px; font-weight: 700; color: var(--green); line-height: 24px; text-transform: uppercase; }
  .person-title { font-size: 15px; color: var(--grey-text); line-height: 19px; text-transform: uppercase; }
  .divider { position: absolute; left: 40px; right: 36px; top: 203px; height: 1px; background: var(--rule); }

  .contacts { position: absolute; left: 38px; top: 216px; list-style: none; }
  .contacts li {
    display: flex; align-items: center; gap: 7px;
    font-size: 14.5px; color: var(--grey-text); height: 19px;
  }
  .contacts svg { width: 14px; height: 14px; fill: var(--green); }

  .address {
    position: absolute; right: 34px; top: 255px; text-align: right;
    font-size: 14.5px; color: var(--grey-text); line-height: 19px; font-style: normal;
  }
  .footer-band { position: absolute; left: 0; bottom: 0; width: 600px; height: 40px; }
  .footer-url {
    position: absolute; right: 34px; bottom: 12px;
    font-size: 14px; color: var(--white);
  }

  .back-brand {
    position: absolute; right: 34px; top: 182px;
    font-size: 80px; font-weight: 300; color: var(--white); line-height: 1; letter-spacing: -1px;
  }
  .back-url {
    position: absolute; right: 33px; top: 296px;
    font-size: 14px; color: var(--white); letter-spacing: 2.6px;
  }
</style>
</head>
<body>
<div class="canvas">
  <section class="card card-front">
    <div class="brand">
      <span class="brand-mark"></span>
      <span class="brand-name">brovix</span>
    </div>

    <div class="name-bar"></div>
    <div class="person">
      <p class="person-name">Halyna Dorosh</p>
      <p class="person-title">Director of Marketing</p>
    </div>
    <div class="divider"></div>

    <ul class="contacts">
      <li><svg viewBox="0 0 16 16"><path d="M3.5 1l2.6 3-1.3 2c.9 1.9 2.4 3.4 4.3 4.4l2-1.3 3 2.6-1.5 2.6C7 14.3 1.7 9 1 2.5z"/></svg>780.555.0184</li>
      <li><svg viewBox="0 0 16 16"><path d="M4 0h8a1 1 0 0 1 1 1v14a1 1 0 0 1-1 1H4a1 1 0 0 1-1-1V1a1 1 0 0 1 1-1zm1 2v10h6V2zm3 11a1 1 0 1 0 0 2 1 1 0 0 0 0-2z"/></svg>780.555.0147</li>
      <li><svg viewBox="0 0 16 16"><path d="M4 1h8v4H4zM1 6h14v6h-2v-2H3v2H1zm3 5h8v4H4z"/></svg>780.555.0192</li>
      <li><svg viewBox="0 0 16 16"><path d="M1 3h14v1.5L8 9 1 4.5zm0 3l7 4.5L15 6v7H1z"/></svg>halya.dorosh@quillmail.example</li>
    </ul>

    <address class="address">20517 - 87 Ave.<br>Edmonton, AB, Canada. T6K 4N8</address>

    <svg class="footer-band" viewBox="0 0 600 40" preserveAspectRatio="none" aria-hidden="true">
      <rect x="0" y="26" width="345" height="14" fill="var(--grey)"/>
      <path d="M353 0H600V40H337z" fill="var(--green)"/>
    </svg>
    <span class="footer-url">www.brovix.example</span>
  </section>

  <section class="card card-back">
    <p class="back-brand">brovix</p>
    <p class="back-url">www.brovix.example</p>
  </section>
</div>
</body>
</html>
```